tinyTally Resource Book - 10 maths tasks to do outside

I need a 22 (11 pages back to back) page A6 sized book produced to standard for submission to professional printer. Needs to be as .pdf file showing guide lines and allowances for colour bleed. I have text already written and submitted as attachment in a Word file with margins set to A6 size. The theme of the materials is "Nature Play" so using lots of pictures from nature (Australia preferably) and showing lots of patterns in nature (rocks, leaves, flower petals etc). Some of the tasks refer to specific activities, such as "shadows" and "floating" so would be great to illustrate appropriately. The big emphasis is on learning outside the classroom, getting kids to engage actively with nature. I would like to see the pages as full colour - so not white background. The book itself will be spiral bound along the top edge so a margin of at least 1cm will be required at the top of each page (or the bottom of even numbered pages). Book will be printed on plastic laminated matte paper for outdoor use. Font size needs to be big enough to read. Fonts sizes, alignments and page numbers are all different at the moment and need to be standardised. One photo is included in a page as a sample if you can use it, otherwise disregard. Logo for Wattlebrook Numeracy Guild is also included to have as part of the acknowledgements at the back of the book.

Target Market(s)

Book is for early childhood and preschool teachers.

Industry/Entity Type

Education

Font styles to use
Sans Serif

Requirements
Must have
• Colour and appeal.
Nice to have
• Use of natural colours instead of bright catchy colours but that is your call.
Should not have
• American spelling

```html
<!DOCTYPE html>
<html lang="en-AU">
<head>
<meta charset="utf-8">
<title>tinyTally – 6. Stacking</title>
<link rel="stylesheet" href="https://fonts.googleapis.com/css2?family=Nunito:wght@900&family=Didact+Gothic&display=swap">
<style>
  :root {
    --paper: #ffffff;
    --trim: #6b6b6b;
    --sea: #cfcbc3;
    --sand-light: #e8d6bd;
    --sand: #dcc3a3;
    --heading: #2b3990;
    --heading-edge: #ffffff;
    --body: #2a2622;
    --bullet: #e0262b;
    --pebble-dark: #3b3838;
    --pebble-mid: #6a6666;
  }
  * { margin: 0; padding: 0; box-sizing: border-box; }
  html, body { width: 892px; height: 1200px; overflow: hidden; background: var(--paper); }
  .page { position: relative; width: 892px; height: 1200px; }
  .crop-marks { position: absolute; inset: 0; }
  .bleed-photo {
    position: absolute; left: 53px; top: 56px; width: 787px; height: 1092px;
    background:
      radial-gradient(ellipse 260px 560px at 300px 760px, rgba(236,224,206,.75), transparent 70%),
      linear-gradient(180deg, var(--sea) 0%, #dcd6cc 14%, var(--sand-light) 30%, var(--sand) 100%);
  }
  .pebble-photo {
    position: absolute; left: 568px; top: 844px; width: 180px; height: 208px;
    border-radius: 40% 40% 45% 45%;
    background: radial-gradient(ellipse at 40% 35%, var(--pebble-mid), var(--pebble-dark) 70%);
  }
  .heading {
    position: absolute; left: 124px;
    font-family: "Nunito", sans-serif; font-weight: 900;
    font-size: 45px; line-height: 52px; color: var(--heading);
    text-shadow: 2px 0 var(--heading-edge), -2px 0 var(--heading-edge), 0 2px var(--heading-edge), 0 -2px var(--heading-edge),
                 2px 2px var(--heading-edge), -2px -2px var(--heading-edge), 2px -2px var(--heading-edge), -2px 2px var(--heading-edge),
                 3px 3px 4px rgba(0,0,0,.35);
  }
  .heading--title { top: 140px; }
  .heading--prompts { top: 392px; font-size: 40px; }
  .heading--variations { top: 640px; font-size: 40px; }
  .heading--ideas { top: 806px; font-size: 40px; }
  .task-list {
    position: absolute; left: 184px; width: 560px; list-style: none;
    font-family: "Didact Gothic", sans-serif; font-size: 30px; line-height: 42.4px; color: var(--body);
  }
  .task-list li { position: relative; padding-left: 34px; }
  .task-list li::before {
    content: ""; position: absolute; left: 4px; top: 12px; width: 17px; height: 17px;
    background: var(--bullet); transform: rotate(45deg);
  }
  .task-list--steps { top: 201px; }
  .task-list--prompts { top: 450px; }
  .task-list--variations { top: 699px; }
  .task-list--ideas { top: 863px; }
</style>
</head>
<body>
<main class="page">
  <div class="bleed-photo" role="img" aria-label="Photo of a stack of smooth pale stones balanced on a sandy beach with waves behind"></div>
  <div class="pebble-photo" role="img" aria-label="Photo of three small dark pebbles stacked"></div>

  <svg class="crop-marks" width="892" height="1200" viewBox="0 0 892 1200" aria-hidden="true">
    <g stroke="var(--trim)" stroke-width="1" fill="none">
      <path d="M53 0V46M0 53H46M74 36V74M36 74H74"/>
      <path d="M839 0V46M892 53H846M818 36V74M856 74H818"/>
      <path d="M53 1200V1154M0 1147H46M74 1164V1126M36 1126H74"/>
      <path d="M839 1200V1154M892 1147H846M818 1164V1126M856 1126H818"/>
    </g>
  </svg>

  <h1 class="heading heading--title">6. Stacking</h1>
  <ul class="task-list task-list--steps">
    <li>Get 3 stones</li>
    <li>Stack them one on top of the other</li>
    <li>Add another stone to the stack</li>
    <li>Continue until it falls down</li>
  </ul>

  <h2 class="heading heading--prompts">Prompting questions</h2>
  <ul class="task-list task-list--prompts">
    <li>How many stones can you stack?</li>
    <li>What makes them fall down?</li>
    <li>Do you always need to put the big ones on the bottom?</li>
  </ul>

  <h2 class="heading heading--variations">Variations</h2>
  <ul class="task-list task-list--variations">
    <li>Use materials other than stones</li>
    <li>Put the biggest stone on the top</li>
  </ul>

  <h2 class="heading heading--ideas">Big Ideas</h2>
  <ul class="task-list task-list--ideas">
    <li>Prediction</li>
    <li>Balance</li>
    <li>Size</li>
  </ul>
</main>
</body>
</html>
```